professional business card design for technology company

We are a small technology consulting firm, specialising in consulting based around Cloud and Managed services. Our colour scheme is yellow, blue and white, as you can see in the logos. Although we are based in melbourne australia, due to the nature of our work, our clients can be located anywhere. We are looking for a clean, professional, positive look - similar to our company logo

Target Market(s)

small business

Industry/Entity Type

Business

Contact Information for Business Card

eye catching, designed to incorporate some level of raised printing. Must contain website address, phone number, name and job title

Requirements
Must have
• Logo (attached) - use of the same colour scheme

```html
<!DOCTYPE html>
<html lang="en">
<head>
<meta charset="utf-8">
<title>Novacrest Business Card</title>
<link rel="stylesheet" href="https://fonts.googleapis.com/css2?family=Lato:wght@400;700;900&display=swap">
<style>
  :root {
    --bg: #2a2a2c;
    --card-white: #ffffff;
    --card-shade: #e9e9ea;
    --band-blue: #2f93c9;
    --band-blue-dark: #2584b9;
    --stripe-grey: #4a4a4c;
    --ink: #3d3d3f;
    --ink-soft: #555558;
    --accent-blue: #2e8fd0;
    --accent-yellow: #e8b817;
    --band-text: #d6ecf8;
  }
  * { box-sizing: border-box; margin: 0; padding: 0; }
  html, body { width: 1200px; height: 873px; overflow: hidden; }
  body {
    background: var(--bg);
    font-family: "Lato", Arial, sans-serif;
    position: relative;
  }
  .card {
    position: absolute;
    width: 520px;
    height: 300px;
    border-radius: 14px;
    overflow: hidden;
    background: linear-gradient(160deg, var(--card-white) 40%, var(--card-shade) 100%);
    box-shadow: 0 18px 40px rgba(0,0,0,.55);
  }
  .card--front { left: 60px; top: 120px; }
  .card--back { left: 620px; top: 440px; }

  .band {
    position: absolute;
    left: 0; right: 0; bottom: 0;
    height: 78px;
    background: linear-gradient(180deg, var(--band-blue) 0%, var(--band-blue-dark) 100%);
    border-top: 8px solid var(--stripe-grey);
    display: flex;
    align-items: center;
    justify-content: center;
  }
  .band__text {
    color: var(--band-text);
    font-size: 13px;
    letter-spacing: 3.5px;
    font-weight: 400;
  }

  .brand {
    display: flex;
    align-items: center;
    gap: 12px;
    color: var(--ink);
    font-weight: 900;
    letter-spacing: -1px;
  }
  .brand__dot {
    border-radius: 50%;
    background: var(--accent-blue);
    flex: none;
  }
  .card--front .brand {
    position: absolute;
    left: 0; right: 0; top: 78px;
    justify-content: center;
    font-size: 56px;
  }
  .card--front .brand__dot { width: 44px; height: 44px; }

  .card--back .brand {
    position: absolute;
    left: 28px; top: 104px;
    font-size: 36px;
  }
  .card--back .brand__dot { width: 30px; height: 30px; }

  .divider {
    position: absolute;
    left: 258px; top: 22px;
    width: 3px; height: 178px;
    background: linear-gradient(180deg, rgba(46,143,208,0) 0%, var(--accent-blue) 45%, rgba(46,143,208,0) 100%);
  }

  .person {
    position: absolute;
    left: 284px; top: 22px;
  }
  .person__name {
    color: var(--accent-blue);
    font-size: 19px;
    font-weight: 900;
  }
  .person__title {
    color: var(--ink);
    font-size: 12px;
    font-weight: 700;
    margin-top: 2px;
  }

  .contacts {
    position: absolute;
    left: 278px; top: 92px;
    list-style: none;
  }
  .contacts__item {
    display: flex;
    align-items: flex-start;
    gap: 8px;
    color: var(--ink-soft);
    font-size: 13.5px;
    line-height: 16px;
    margin-bottom: 7px;
  }
  .contacts__icon {
    width: 18px; height: 18px;
    border-radius: 50%;
    background: var(--accent-yellow);
    flex: none;
    display: flex;
    align-items: center;
    justify-content: center;
  }
  .contacts__icon svg { width: 11px; height: 11px; fill: #fff; }
</style>
</head>
<body>

  <section class="card card--front" aria-label="Business card front">
    <div class="brand">
      <span class="brand__dot"></span>
      <span class="brand__name">Novacrest</span>
    </div>
    <div class="band">
      <span class="band__text">Your slogan / Tagline Here</span>
    </div>
  </section>

  <section class="card card--back" aria-label="Business card back">
    <div class="brand">
      <span class="brand__dot"></span>
      <span class="brand__name">Novacrest</span>
    </div>

    <div class="divider"></div>

    <div class="person">
      <p class="person__name">Dana Whitlock</p>
      <p class="person__title">Owner / Founder</p>
    </div>

    <ul class="contacts">
      <li class="contacts__item">
        <span class="contacts__icon">
          <svg viewBox="0 0 24 24"><path d="M6.6 10.8a15 15 0 0 0 6.6 6.6l2.2-2.2a1 1 0 0 1 1-.25 11.4 11.4 0 0 0 3.6.57 1 1 0 0 1 1 1V20a1 1 0 0 1-1 1A17 17 0 0 1 3 4a1 1 0 0 1 1-1h3.5a1 1 0 0 1 1 1c0 1.25.2 2.45.57 3.6a1 1 0 0 1-.25 1z"/></svg>
        </span>
        <span>555-014-2280 x214</span>
      </li>
      <li class="contacts__item">
        <span class="contacts__icon">
          <svg viewBox="0 0 24 24"><path d="M2 5h20v14H2z M2 5l10 8 10-8" fill="#fff"/><path d="M3 6l9 7 9-7" stroke="#e8b817" stroke-width="2" fill="none"/></svg>
        </span>
        <span>800-555-0199</span>
      </li>
      <li class="contacts__item">
        <span class="contacts__icon">
          <svg viewBox="0 0 24 24"><path d="M10 14a4 4 0 0 1 0-5.6l3-3a4 4 0 0 1 5.6 5.6l-1.5 1.5-1.4-1.4 1.5-1.5a2 2 0 0 0-2.8-2.8l-3 3a2 2 0 0 0 0 2.8zm4-4a4 4 0 0 1 0 5.6l-3 3a4 4 0 0 1-5.6-5.6l1.5-1.5 1.4 1.4-1.5 1.5a2 2 0 0 0 2.8 2.8l3-3a2 2 0 0 0 0-2.8z"/></svg>
        </span>
        <span>dwhitlock@novacrest.com</span>
      </li>
      <li class="contacts__item">
        <span class="contacts__icon">
          <svg viewBox="0 0 24 24"><path d="M12 2a7 7 0 0 0-7 7c0 5 7 13 7 13s7-8 7-13a7 7 0 0 0-7-7zm0 9.5A2.5 2.5 0 1 1 12 6.5a2.5 2.5 0 0 1 0 5z"/></svg>
        </span>
        <span>118 Harbour Lane East<br>Suite 400, Canada, K0A 1B2</span>
      </li>
    </ul>

    <div class="band">
      <span class="band__text">www.novacrest.com</span>
    </div>
  </section>

</body>
</html>
```